Business card por a urban DJ, up scale audience target

Need a sober design, modern, conservative colors but i can consider some options, y play rnb, hip hop, EDM and top40.

Business card for contact and personal info, double sided, use logo attrached please; im 42 so i need a card acording to my age an target audience.

Target Market(s)

Adult people, up scale audience

Industry/Entity Type

Music Download

Contact Information for Business Card

Cel (318) 4207265518 www.lumadrift.com

Requirements
Must have
• open mind
Nice to have
• open mind
Should not have
• DJ

```html
<!DOCTYPE html>
<html lang="en">
<head>
<meta charset="utf-8">
<title>Luma Drift – Business Card</title>
<link rel="stylesheet" href="https://fonts.googleapis.com/css2?family=Open+Sans:wght@400;700;800&display=swap">
<style>
  :root {
    --stage: #2b2b2b;
    --card: #050505;
    --ghost: #1d1d1d;
    --silver: #b9b9bb;
    --muted: #8a8a8c;
    --rule: #555;
  }
  * { margin: 0; padding: 0; box-sizing: border-box; }
  html, body { width: 1200px; height: 900px; overflow: hidden; }
  body {
    background: var(--stage);
    font-family: "Open Sans", sans-serif;
    position: relative;
  }
  .card {
    position: absolute;
    left: 250px;
    width: 700px;
    height: 400px;
    background: var(--card);
    overflow: hidden;
    box-shadow: 0 10px 30px rgba(0,0,0,.5);
  }
  .card-front { top: 40px; }
  .card-back { top: 460px; }

  .wordmark {
    font-weight: 800;
    color: var(--silver);
    letter-spacing: 4px;
    line-height: 1;
  }
  .card-front .wordmark {
    position: absolute;
    left: 0; right: 0;
    top: 50%;
    transform: translateY(-50%);
    text-align: center;
    font-size: 120px;
  }
  .ghost-mark {
    position: absolute;
    left: 80px;
    bottom: 60px;
    font-size: 260px;
    font-weight: 800;
    color: var(--ghost);
    letter-spacing: 10px;
    line-height: 1;
  }
  .card-back .wordmark {
    position: absolute;
    right: 40px;
    top: 40px;
    font-size: 84px;
  }
  .divider {
    position: absolute;
    left: 300px;
    right: 0;
    top: 150px;
    border-top: 1px solid var(--rule);
  }
  .contact {
    position: absolute;
    left: 34px;
    top: 215px;
    color: var(--silver);
  }
  .contact .name { font-size: 20px; font-weight: 700; }
  .contact .role { font-size: 12px; color: var(--muted); margin-bottom: 6px; }
  .contact .line {
    display: flex; align-items: center; gap: 8px;
    font-size: 13px; color: var(--muted); margin-top: 2px;
  }
  .contact svg { width: 11px; height: 11px; }
  .equalizer {
    position: absolute;
    left: 0; bottom: 0;
    width: 700px; height: 120px;
  }
  .equalizer rect { fill: var(--silver); }
</style>
</head>
<body>
  <section class="card card-front">
    <div class="wordmark">LUMA</div>
  </section>

  <section class="card card-back">
    <div class="ghost-mark" aria-hidden="true">LUMA</div>
    <div class="wordmark">LUMA</div>
    <div class="divider"></div>

    <div class="contact">
      <div class="name">Marco Vell</div>
      <div class="role">CEO</div>
      <div class="line">
        <svg viewBox="0 0 12 12" aria-hidden="true"><rect x="3" y="0.5" width="6" height="11" rx="1" fill="none" stroke="#8a8a8c"/><circle cx="6" cy="9.5" r=".8" fill="#8a8a8c"/></svg>
        <span>(318) 4207265518</span>
      </div>
      <div class="line">
        <svg viewBox="0 0 12 12" aria-hidden="true"><circle cx="6" cy="6" r="5" fill="none" stroke="#8a8a8c"/><ellipse cx="6" cy="6" rx="2.2" ry="5" fill="none" stroke="#8a8a8c"/><line x1="1" y1="6" x2="11" y2="6" stroke="#8a8a8c"/></svg>
        <span>www.lumadrift.com</span>
      </div>
    </div>

    <svg class="equalizer" viewBox="0 0 700 120" aria-hidden="true">
      <rect x="30" y="66" width="9" height="46"/>
      <rect x="44" y="72" width="9" height="40"/>
      <rect x="58" y="60" width="9" height="52"/>
      <rect x="72" y="80" width="9" height="32"/>
      <rect x="86" y="70" width="9" height="42"/>
      <rect x="100" y="92" width="9" height="20"/>
      <rect x="114" y="76" width="9" height="36"/>
      <rect x="128" y="62" width="9" height="50"/>
      <rect x="142" y="84" width="9" height="28"/>
      <rect x="156" y="74" width="9" height="38"/>
      <rect x="170" y="98" width="9" height="14"/>
      <rect x="184" y="82" width="9" height="30"/>
      <rect x="198" y="104" width="9" height="8"/>
      <rect x="212" y="86" width="9" height="26"/>
      <rect x="226" y="100" width="9" height="12"/>
      <rect x="240" y="72" width="9" height="40"/>
      <rect x="254" y="90" width="9" height="22"/>
      <rect x="268" y="64" width="9" height="48"/>
      <rect x="282" y="86" width="9" height="26"/>
      <rect x="296" y="74" width="9" height="38"/>
      <rect x="310" y="92" width="9" height="20"/>
      <rect x="324" y="80" width="9" height="32"/>
      <rect x="338" y="52" width="9" height="60"/>
      <rect x="352" y="70" width="9" height="42"/>
      <rect x="366" y="84" width="9" height="28"/>
      <rect x="380" y="60" width="9" height="52"/>
      <rect x="394" y="78" width="9" height="34"/>
      <rect x="408" y="94" width="9" height="18"/>
      <rect x="422" y="66" width="9" height="46"/>
      <rect x="436" y="86" width="9" height="26"/>
      <rect x="450" y="104" width="9" height="8"/>
      <rect x="464" y="106" width="9" height="6"/>
      <rect x="478" y="96" width="9" height="16"/>
      <rect x="492" y="80" width="9" height="32"/>
      <rect x="506" y="70" width="9" height="42"/>
      <rect x="520" y="88" width="9" height="24"/>
      <rect x="534" y="62" width="9" height="50"/>
      <rect x="548" y="50" width="9" height="62"/>
      <rect x="562" y="72" width="9" height="40"/>
      <rect x="576" y="88" width="9" height="24"/>
      <rect x="590" y="58" width="9" height="54"/>
      <rect x="604" y="84" width="9" height="28"/>
      <rect x="618" y="44" width="9" height="68"/>
      <rect x="632" y="30" width="9" height="82"/>
      <rect x="646" y="16" width="9" height="96"/>
      <rect x="660" y="8" width="9" height="104"/>
    </svg>
  </section>
</body>
</html>
```